Business card design for Automotive workshop

We need a business card for a new automotive repair and tyre shop called Keelstone Prime Automotive located in New Zealand. We are a clean, modern and fresh workshop and company.

Front needs to feature logo,
my name:
Marlo Fenwicke (director)

Address:
48 Tarn Lane
Harrowmere 3642

Phone: 07 594 2713
Mobile: 027 451 9362
Email: office@keelstoneautomotive.example.nz
Website: keelstoneautomotive.example.nz

Back needs to feature an area to write down appointment details, date and time.

Also feature a list of jobs and work we do such as,
Vehicle Servicing
All Mechanical Repairs
Warrant of Fitness
Tyres & Wheel Alignments
Automotive Diagnostics
Automotive Parts & Supplies

```html
<!DOCTYPE html>
<html lang="en">
<head>
<meta charset="utf-8">
<title>Keelstone Prime Automotive – Business Card</title>
<link rel="stylesheet" href="https://fonts.googleapis.com/css2?family=Open+Sans:wght@400;600;700;800&display=swap">
<style>
  :root {
    --page: #9a9a9a;
    --card-light: #fbfcfd;
    --card-cool: #e9eef3;
    --ink: #1d1d1f;
    --ink-soft: #333336;
    --red: #e3262b;
  }
  * { box-sizing: border-box; margin: 0; padding: 0; }
  html, body { width: 1200px; height: 800px; overflow: hidden; }
  body {
    background: var(--page);
    font-family: "Open Sans", Arial, sans-serif;
    color: var(--ink);
    display: flex;
    align-items: center;
    justify-content: center;
    gap: 40px;
  }
  .card {
    position: relative;
    width: 540px;
    height: 310px;
    border-radius: 18px;
    background:
      radial-gradient(ellipse at 30% 35%, var(--card-cool) 0%, transparent 55%),
      radial-gradient(ellipse at 75% 70%, var(--card-cool) 0%, transparent 50%),
      var(--card-light);
    box-shadow: 0 6px 18px rgba(0,0,0,.25);
    overflow: hidden;
  }
  .brand {
    position: absolute;
    display: flex;
    align-items: center;
    gap: 8px;
    color: var(--red);
    font-weight: 800;
    text-transform: uppercase;
    letter-spacing: .04em;
    line-height: 1.05;
    font-size: 25px;
  }
  .brand-mark {
    width: 12px; height: 12px;
    background: var(--red);
    flex: none;
  }

  /* Front */
  .card-front .brand { left: 36px; top: 42px; }
  .front-rule {
    position: absolute;
    left: 0; top: 146px;
    width: 200px; height: 2px;
    background: var(--red);
  }
  .contact {
    position: absolute;
    left: 206px; top: 134px;
    font-size: 13.5px;
    line-height: 1.4;
    color: var(--ink-soft);
  }
  .contact-name { font-weight: 700; font-size: 16px; color: var(--ink); }
  .contact-role { color: var(--red); font-size: 13px; margin-bottom: 2px; }
  .contact-line { display: flex; align-items: center; gap: 7px; }
  .contact-line svg { width: 12px; height: 12px; flex: none; }

  /* Back */
  .card-back .brand { right: 36px; top: 38px; }
  .services {
    position: absolute;
    left: 188px; top: 108px;
    list-style: none;
    display: grid;
    grid-template-columns: auto auto;
    column-gap: 22px;
    row-gap: 8px;
    font-size: 11.5px;
    color: var(--ink-soft);
  }
  .services li { display: flex; align-items: center; gap: 5px; }
  .services li::before {
    content: "";
    width: 5px; height: 5px; border-radius: 50%;
    background: var(--red);
  }
  .appointment {
    position: absolute;
    left: 40px; bottom: 46px;
    display: flex;
    flex-direction: column;
    gap: 34px;
    font-size: 15px;
    color: var(--ink-soft);
  }
  .appointment-field { display: flex; align-items: flex-end; gap: 6px; }
  .appointment-line {
    display: inline-block;
    width: 150px;
    border-bottom: 1px solid var(--ink-soft);
    margin-bottom: 4px;
  }
</style>
</head>
<body>

  <section class="card card-front" aria-label="Business card front">
    <div class="brand"><span class="brand-mark"></span><span>Keelstone Prime<br>Automotive</span></div>
    <div class="front-rule"></div>
    <div class="contact">
      <p class="contact-name">Marlo Fenwicke</p>
      <p class="contact-role">Managing Director</p>
      <p>48 Tarn Lane</p>
      <p>Harrowmere 3642</p>
      <p class="contact-line">
        <svg viewBox="0 0 12 12" aria-hidden="true"><rect x="3" y="0.5" width="6" height="11" rx="1" fill="none" stroke="#e3262b" stroke-width="1.2"/><circle cx="6" cy="9.5" r=".8" fill="#e3262b"/></svg>
        + 027 451 9362
      </p>
      <p class="contact-line">
        <svg viewBox="0 0 12 12" aria-hidden="true"><path d="M1 4 Q6 0 11 4 L9.5 5.5 L8 4.5 L4 4.5 L2.5 5.5 Z" fill="#e3262b"/><rect x="3" y="6" width="6" height="5" rx="1" fill="#e3262b"/></svg>
        + 07 594 2713
      </p>
      <p class="contact-line">
        <svg viewBox="0 0 12 12" aria-hidden="true"><rect x=".8" y="2.5" width="10.4" height="7" fill="none" stroke="#e3262b" stroke-width="1.2"/><path d="M1 3 L6 7 L11 3" fill="none" stroke="#e3262b" stroke-width="1.2"/></svg>
        office@keelstoneautomotive.example.nz
      </p>
      <p class="contact-line">
        <svg viewBox="0 0 12 12" aria-hidden="true"><circle cx="6" cy="6" r="5" fill="none" stroke="#e3262b" stroke-width="1.2"/><path d="M1 6 H11 M6 1 Q3 6 6 11 M6 1 Q9 6 6 11" fill="none" stroke="#e3262b" stroke-width="1"/></svg>
        keelstoneautomotive.example.nz
      </p>
    </div>
  </section>

  <section class="card card-back" aria-label="Business card back">
    <div class="brand"><span class="brand-mark"></span><span>Keelstone Prime<br>Automotive</span></div>
    <ul class="services">
      <li>Vehicle Servicing</li>
      <li>All Mechanical Repairs</li>
      <li>Warrant of Fitness</li>
      <li>Tyres &amp; Wheel Alignments</li>
      <li>Automotive Diagnostics</li>
      <li>Automotive Parts &amp; Supplies</li>
    </ul>
    <div class="appointment">
      <p class="appointment-field">Date <span class="appointment-line"></span></p>
      <p class="appointment-field">Time <span class="appointment-line"></span></p>
    </div>
  </section>

</body>
</html>
```